IT Company requires new Business Card design.

Over the years we have had a few different business card designs. We are now due for new cards across the board for all staff. We felt this would be a good time to start fresh with a new design. Our traditional card simply had our details on the front, and a list of services on the back. We don't particularly need the list of services, we have had cards where the only thing on the rear of the card was our logo.
Feel free to be creative, we would like our tag line "Complete IT Management" to appear at some point, doesn't necessarily have to be with the logo.
I have attached samples and drafts of various previous cards we have used over the years.

```html
<!DOCTYPE html>
<html lang="en">
<head>
<meta charset="utf-8">
<title>Harbor Systems – Business Card</title>
<link rel="stylesheet" href="https://fonts.googleapis.com/css2?family=Open+Sans:wght@400;600;700&display=swap">
<style>
  :root {
    --backdrop: #e6e6e4;
    --card: #ffffff;
    --slate: #5d6b77;
    --band-dark: #4f5459;
    --text: #4a4d50;
    --divider: #c9ccd0;
    --white: #ffffff;
  }
  * { box-sizing: border-box; margin: 0; padding: 0; }
  html, body {
    width: 1034px; height: 1200px; overflow: hidden;
    background: var(--backdrop);
    font-family: "Open Sans", Arial, sans-serif;
    color: var(--text);
  }
  .card {
    position: absolute; left: 74px; width: 898px; height: 511px;
    background: var(--card);
    overflow: hidden;
    box-shadow: 0 2px 6px rgba(0,0,0,.18);
  }
  .card--front { top: 69px; }
  .card--back { top: 631px; }

  /* front: brand */
  .brand {
    position: absolute; left: 51px; top: 166px; width: 380px;
    display: flex; align-items: center; gap: 20px;
  }
  .brand__mark { width: 96px; height: 96px; background: var(--slate); flex: none; }
  .brand__name {
    font-weight: 700; font-size: 44px; line-height: 1.05;
    color: var(--slate); letter-spacing: .5px;
  }
  .divider {
    position: absolute; left: 459px; top: 48px; width: 2px; height: 381px;
    background: var(--divider);
  }

  /* front: details */
  .details { position: absolute; left: 487px; top: 50px; }
  .details__name { font-weight: 700; font-size: 27px; color: var(--slate); line-height: 1.2; }
  .details__role { font-size: 21px; line-height: 1.3; margin-bottom: 24px; }
  .contact { list-style: none; }
  .contact__item {
    display: flex; align-items: center; gap: 10px;
    font-size: 21px; line-height: 36px;
  }
  .contact__icon { width: 20px; height: 20px; fill: var(--slate); flex: none; }
  .address { margin-top: 22px; font-size: 21px; line-height: 31px; }

  /* front: bands */
  .band { position: absolute; display: block; }
  .band--left { left: 0; bottom: 0; }
  .band--tag { right: 0; bottom: 0; }
  .tagline {
    position: absolute; right: 68px; bottom: 12px;
    color: var(--white); font-size: 22px; font-weight: 400;
  }

  /* back */
  .back-brand {
    position: absolute; left: 0; right: 0; top: 175px;
    display: flex; justify-content: center; align-items: center; gap: 26px;
  }
  .back-brand__mark { width: 90px; height: 90px; background: var(--slate); }
  .back-brand__name { font-weight: 700; font-size: 62px; color: var(--slate); line-height: 1; }
  .back-web {
    position: absolute; left: 0; right: 0; top: 466px; text-align: center;
    font-size: 26px; letter-spacing: 2px; color: var(--text);
  }
</style>
</head>
<body>
  <section class="card card--front">
    <div class="brand">
      <span class="brand__mark"></span>
      <span class="brand__name">HARBOR<br>SYSTEMS</span>
    </div>
    <div class="divider"></div>

    <div class="details">
      <p class="details__name">Daniel Reeve</p>
      <p class="details__role">Operation Manager</p>
      <ul class="contact">
        <li class="contact__item">
          <svg class="contact__icon" viewBox="0 0 20 20"><path d="M5 2l3 4-2 2c1 2.5 3.5 5 6 6l2-2 4 3-2 3C9 18 2 11 2 4z"/></svg>
          08 9320 5180
        </li>
        <li class="contact__item">
          <svg class="contact__icon" viewBox="0 0 20 20"><path d="M6 1h8a1 1 0 0 1 1 1v16a1 1 0 0 1-1 1H6a1 1 0 0 1-1-1V2a1 1 0 0 1 1-1zm1 3v9h6V4zm3 11a1.2 1.2 0 1 0 0 2.4A1.2 1.2 0 0 0 10 15z"/></svg>
          0412 608 947
        </li>
        <li class="contact__item">
          <svg class="contact__icon" viewBox="0 0 20 20"><path d="M6 2h7v5H6zM3 8h14a1 1 0 0 1 1 1v8H2V9a1 1 0 0 1 1-1zm2 3v2h10v-2z"/></svg>
          08 9320 5180
        </li>
        <li class="contact__item">
          <svg class="contact__icon" viewBox="0 0 20 20"><path d="M2 4h16v12H2zm1.5 1.5L10 11l6.5-5.5z" fill-rule="evenodd"/></svg>
          daniel@harborsystems.com.au
        </li>
        <li class="contact__item">
          <svg class="contact__icon" viewBox="0 0 20 20" fill="none" stroke="var(--slate)" stroke-width="1.6"><circle cx="10" cy="10" r="8"/><ellipse cx="10" cy="10" rx="3.5" ry="8"/><path d="M2 10h16"/></svg>
          www.harborsystems.com.au
        </li>
      </ul>
      <p class="address">Unit 4 18 Kestrel Road<br>Southport WA 6170</p>
    </div>

    <svg class="band band--left" width="470" height="32" viewBox="0 0 470 32" aria-hidden="true">
      <polygon points="0,2 466,2 448,32 0,32" fill="var(--band-dark)"/>
    </svg>
    <svg class="band band--tag" width="430" height="52" viewBox="0 0 430 52" aria-hidden="true">
      <polygon points="20,0 430,0 430,52 0,52" fill="var(--slate)"/>
    </svg>
    <p class="tagline">Complete IT Management</p>
  </section>

  <section class="card card--back">
    <div class="back-brand">
      <span class="back-brand__mark"></span>
      <span class="back-brand__name">HARBOR SYSTEMS</span>
    </div>
    <p class="back-web">www.harborsystems.com.au</p>
  </section>
</body>
</html>
```